Software Development Consulting Company Needs Business Card Design

We need a new business card design for our consultants at Kestrel Works (kestrelworks.example). We are a small firm that provides high-end software development and methodology consulting to medium to large enterprise IT organizations.

Our logo uses Futura for the font and we would like to stick with navy blue and canary yellow for the logo colors. Attached are normal and reversed versions of our logos in illustrator format.
Updates

Hi Everyone, Thank yo very much for your amazing design ideas. I have created a poll for this project and our employees will be voting on the design they wish to use. We will be making a decision this Wednesday (October 22nd). Thanks again, Dale Hartwick

Industry/Entity Type

Business

```html
<!DOCTYPE html>
<html lang="en">
<head>
<meta charset="utf-8">
<title>Kestrel Works – Business Card</title>
<link href="https://fonts.googleapis.com/css2?family=Jost:wght@400;500&family=Open+Sans:wght@400;700&display=swap" rel="stylesheet">
<style>
  :root {
    --navy: #1f4468;
    --canary: #ffe600;
    --white: #ffffff;
    --ink: #2a3a4c;
    --rule: #c9ced4;
    --backdrop: #e9eaec;
  }
  * { box-sizing: border-box; margin: 0; padding: 0; }
  html, body {
    width: 1200px; height: 720px; overflow: hidden;
    background: var(--backdrop);
  }
  .canvas { position: relative; width: 1200px; height: 720px; }
  .card {
    position: absolute; top: 211px;
    width: 525px; height: 300px;
    overflow: hidden;
    box-shadow: 0 6px 18px rgba(0,0,0,.18);
  }
  .card--front { left: 50px; background: var(--white); }
  .card--back { left: 625px; background: var(--navy); }

  .accent-band {
    position: absolute; left: 250px; right: 0; top: 0; height: 62px;
    background: var(--canary);
  }
  .accent-rule {
    position: absolute; left: 250px; right: 0; top: 62px; height: 10px;
    background: var(--navy);
  }

  .holder {
    position: absolute; right: 22px; top: 12px; text-align: right;
    font-family: "Open Sans", sans-serif; color: var(--navy);
  }
  .holder__name { font-size: 17px; font-weight: 700; line-height: 1.2; }
  .holder__title { font-size: 11px; color: var(--ink); line-height: 1.3; }

  .brand {
    position: absolute; display: flex; align-items: center; gap: 12px;
    font-family: "Jost", sans-serif; font-weight: 400;
    letter-spacing: .14em; text-transform: uppercase; white-space: nowrap;
  }
  .brand__dot {
    width: 14px; height: 14px; border-radius: 50%; background: var(--canary);
    flex: none;
  }
  .card--front .brand { left: 32px; top: 122px; font-size: 30px; color: var(--navy); }
  .card--back .brand { left: 0; right: 0; top: 104px; justify-content: center; font-size: 34px; color: var(--white); }

  .contact {
    position: absolute; left: 30px; bottom: 24px; list-style: none;
    font-family: "Open Sans", sans-serif; font-size: 12.5px; color: var(--ink);
  }
  .contact li { display: flex; align-items: center; gap: 8px; line-height: 22px; }
  .contact svg { width: 12px; height: 12px; fill: var(--navy); flex: none; }

  .divider {
    position: absolute; left: 272px; bottom: 30px; width: 1px; height: 60px;
    background: var(--rule);
  }
  .offices {
    position: absolute; left: 290px; bottom: 72px; display: flex; gap: 8px;
    font-family: "Open Sans", sans-serif; font-size: 12.5px; color: var(--ink); line-height: 17px;
  }
  .offices svg { width: 12px; height: 16px; fill: var(--navy); flex: none; margin-top: 1px; }

  .web {
    position: absolute; left: 0; right: 0; top: 196px; text-align: center;
    font-family: "Open Sans", sans-serif; font-size: 18px; letter-spacing: .16em;
    color: var(--white);
  }
</style>
</head>
<body>
<main class="canvas">

  <section class="card card--front" aria-label="Business card front">
    <div class="accent-band"></div>
    <div class="accent-rule"></div>
    <div class="holder">
      <p class="holder__name">Your Name</p>
      <p class="holder__title">Title</p>
    </div>
    <div class="brand"><span class="brand__dot"></span>Kestrel Works</div>

    <ul class="contact">
      <li>
        <svg viewBox="0 0 24 24"><path d="M6.6 10.8a15.5 15.5 0 0 0 6.6 6.6l2.2-2.2a1 1 0 0 1 1-.25 11.4 11.4 0 0 0 3.6.57 1 1 0 0 1 1 1V20a1 1 0 0 1-1 1A17 17 0 0 1 3 4a1 1 0 0 1 1-1h3.5a1 1 0 0 1 1 1c0 1.25.2 2.45.57 3.57a1 1 0 0 1-.25 1z"/></svg>
        555-010-2468
      </li>
      <li>
        <svg viewBox="0 0 24 24"><path d="M2 5h20v14H2z M2 5l10 8 10-8" fill="none" stroke="var(--navy)" stroke-width="2.4"/></svg>
        info@kestrelworks.example
      </li>
      <li>
        <svg viewBox="0 0 24 24"><circle cx="12" cy="12" r="9.5" fill="none" stroke="var(--navy)" stroke-width="2.4"/><path d="M2.5 12h19M12 2.5c-5 6-5 13 0 19M12 2.5c5 6 5 13 0 19" fill="none" stroke="var(--navy)" stroke-width="1.8"/></svg>
        www.kestrelworks.example
      </li>
    </ul>

    <div class="divider"></div>
    <div class="offices">
      <svg viewBox="0 0 24 32"><path d="M12 0a12 12 0 0 0-12 12c0 9 12 20 12 20s12-11 12-20A12 12 0 0 0 12 0zm0 17a5 5 0 1 1 0-10 5 5 0 0 1 0 10z"/></svg>
      <p>Riverton<br>Maple Falls, IL</p>
    </div>
  </section>

  <section class="card card--back" aria-label="Business card back">
    <div class="brand"><span class="brand__dot"></span>Kestrel Works</div>
    <p class="web">www.kestrelworks.example</p>
  </section>

</main>
</body>
</html>
```